Im want a website LIKE VRX's and FleetHollow.com's with product payment options like Trenzo's

I need a website LIKE VRX with a header made EXACTLY LIKE THAT OF FLEETHOLLOWS .

The front page photo should be like that of FLEETHOLLOW's webpage as well.

The name of the website will be called "M.K. (Caldera Key)".

We will be targeting ALL MARKETS in a small town in central Panama and charging businesses "listing fees" like a phone book does but also providing informational blogs, news, and other interesting activities.

THIS IS A MULTI PAGE WEBSITE

THIS IS WHERE VRX's website meets Brivelle/FleetHollow.

Once the layout is built I will tweak and modify, add information, and upload items for sale.

Here is a list of specific categories that should be listed out above the front page header image/search bar

-- Home -- News -- Travel -- Activities -- Shop & Dine -- Store -- More... --

These categories should be spread across the bottom of the page in three sections:

WHATS SO GREAT ABOUT (Caldera Key),
HAND PICKED TOURS
ACTIVITIES etc.

Also lets use www.Trenzo.example 's
"HOT DESTINATIONS"
"BEAT THE BEST PRICES IN BOQUETE"
"OCTOBERS INSIDER PICKS"
"TOP DESTINATIONS"
and spread them in four sections side-by-side near the bottom of the page.

Overall I would like to see the finished product to be something LIKE VRX's and FleetHollows.

WE NEED ONLINE PAYMENT OPTIONS LIKE BRIVELLE'S WEBSITE HAS

This will be a desktop website but should be very mobile friendly as well.

-rodmund

P.S. Good luck!

If it isn't already too late to change the website name, the name of the website should be "Caldera Key". Added Friday, October 9, 2015

What do you guys think the budget should be to win this? Added Saturday, October 10, 2015

www.palmorra.example is the most amazing simple site. Whoever can make me a replica with my specifications will win immediately!!!! Added Sunday, October 18, 2015

OMG www.palmorra.example is the bomb!So simple and elegant. Whoever can make me an EXACT REPLICA OF WWW.PALMORRA.EXAMPLE as my site with the specifications mentioned in my brief will take home the $825.00 immediately! Good luck amigos! Added Sunday, October 18, 2015

Does anybody know how to add recurring monthly billing options on this website? Added Sunday, October 18, 2015

ALL MARKETS

Product

Coded - Design and coding required

5+ page

• Coinvey payment options.
• I must be able to add and remove photos/text and video from the HTML files in the page.
• Be creative my friends, and may the odds be forever in your favor!
• I added some photos of a good layout for our page below.

```html
<!DOCTYPE html>
<html lang="en">
<head>
<meta charset="utf-8">
<title>Caldera Key – Travel us with best deals</title>
<link rel="stylesheet" href="https://fonts.googleapis.com/css2?family=Roboto:wght@300;400;500;700;900&family=Roboto+Slab:wght@400;700&display=swap">
<style>
:root{
  --blue:#1e9be0;
  --blue-dark:#1581c0;
  --yellow:#f7cf1e;
  --ink:#222;
  --text:#555;
  --muted:#8a8a8a;
  --dark:#2a2a2a;
  --darker:#1e1e1e;
  --red:#e3262b;
  --line:#e3e3e3;
  --white:#fff;
}
*{box-sizing:border-box;margin:0;padding:0}
html,body{width:1200px;height:3528px;overflow:hidden}
body{font-family:"Roboto",Arial,sans-serif;color:var(--text);background:var(--white);font-size:13px;position:relative}
.wrap{width:1000px;margin:0 auto;position:relative}
a{color:inherit;text-decoration:none}
.btn{display:inline-block;font-size:12px;font-weight:500;padding:0 20px;height:32px;line-height:30px;border:1px solid var(--line);background:var(--white);color:var(--ink)}
.btn-blue{background:var(--blue);border-color:var(--blue);color:var(--white)}
.btn-yellow{background:var(--yellow);border-color:var(--yellow);color:var(--ink)}
.btn-ghost{background:transparent;border-color:rgba(255,255,255,.8);color:var(--white)}
.btn-dark{background:#3a3a3a;border-color:#3a3a3a;color:var(--white)}
.section-title{font-family:"Roboto",Arial,sans-serif;font-weight:700;font-size:26px;color:var(--ink);text-align:center;letter-spacing:.5px}
.photo{display:block}

/* HERO */
.hero{position:absolute;top:0;left:0;width:1200px;height:592px;background:linear-gradient(180deg,#2b88c8 0%,#4fb2de 35%,#7cc7d9 62%,#3f7d8e 82%,#283a42 100%)}
.hero-photo{position:absolute;inset:0;background:radial-gradient(ellipse at 58% 52%,rgba(247,205,150,.55) 0,rgba(247,205,150,0) 22%),linear-gradient(180deg,rgba(0,0,0,0) 60%,rgba(0,0,0,.35) 100%)}
.topbar{position:absolute;top:0;left:0;width:100%;height:40px;background:rgba(0,0,0,.55);color:#eee;font-size:12px}
.topbar .wrap{display:flex;justify-content:space-between;align-items:center;height:40px}
.topbar ul{display:flex;gap:22px;list-style:none}
.topbar li{font-weight:500}
.header{position:absolute;top:52px;left:100px;width:1000px;height:46px;display:flex;align-items:center;background:var(--blue)}
.brand{height:46px;width:150px;background:var(--white);display:flex;align-items:center;gap:8px;padding-left:14px}
.brand-dot{width:12px;height:12px;border-radius:50%;background:var(--blue)}
.brand-name{font-weight:700;font-size:17px;color:var(--blue)}
.nav{display:flex;list-style:none;margin-left:14px}
.nav li{color:var(--white);font-size:12px;font-weight:500;padding:0 16px;line-height:46px}
.nav li.active{background:var(--blue-dark)}
.nav-search{margin-left:auto;margin-right:10px;width:170px;height:28px;border-bottom:1px solid rgba(255,255,255,.7);display:flex;align-items:center;justify-content:space-between;color:rgba(255,255,255,.85);font-size:12px;padding:0 4px}
.hero-copy{position:absolute;top:206px;left:0;width:100%;text-align:center;color:var(--white)}
.hero-copy h1{font-size:46px;font-weight:700;letter-spacing:1px}
.hero-copy .lead{font-size:17px;font-weight:700;margin-top:8px;letter-spacing:.5px}
.hero-copy .note{display:inline-block;margin-top:14px;font-size:12px;background:rgba(0,0,0,.35);padding:3px 12px}
.hero-actions{margin-top:30px;display:flex;justify-content:center;gap:22px}
.search-tours{position:absolute;top:482px;left:100px;width:1000px;height:88px;background:rgba(20,20,20,.82);display:flex;align-items:center;padding:0 22px;gap:14px}
.search-head{width:180px;color:var(--white)}
.search-head strong{display:block;font-size:15px;font-weight:700}
.search-head span{font-size:11px;color:#bbb}
.field{width:140px;height:32px;border:1px solid rgba(255,255,255,.35);color:#ccc;font-size:11px;line-height:30px;padding:0 10px}
.field.wide{width:148px}
.search-tours .btn{margin-left:14px}

/* POPULAR */
.popular{position:absolute;top:592px;left:0;width:1200px;height:576px;background:var(--white)}
.popular-band{position:absolute;top:0;left:0;width:100%;height:224px;background:var(--yellow)}
.popular .section-title{position:absolute;top:40px;width:100%}
.tour-cards{position:absolute;top:92px;left:190px;width:820px;display:flex;justify-content:space-between}
.tour-card{width:250px;background:var(--white);border:1px solid var(--line);text-align:center;padding-bottom:18px;position:relative}
.tour-card .photo{height:190px;margin:10px}
.ribbon{position:absolute;top:26px;right:0;background:var(--blue);color:var(--white);font-size:10px;font-weight:700;padding:5px 10px}
.tour-card h3{font-size:15px;font-weight:700;color:var(--ink);margin-top:14px}
.tour-card p{font-size:12px;line-height:17px;padding:0 20px;margin-top:14px}
.stars{margin-top:12px;display:flex;justify-content:center;gap:2px}
.reviews{font-size:10px;color:var(--muted);margin-top:4px}
.tour-card .btn{margin-top:14px;height:28px;line-height:26px}
.round-badge{position:absolute;top:90px;left:50%;margin-left:-18px;width:36px;height:36px;border-radius:50%;background:var(--white);opacity:.9}

/* TOUR TYPES */
.types{position:absolute;top:1168px;left:0;width:1200px;height:540px;background:linear-gradient(180deg,#3b3a3a 0%,#2c2c2d 50%,#444 100%)}
.types .section-title{position:absolute;top:84px;width:100%;color:var(--white)}
.type-panels{position:absolute;top:132px;left:100px;width:1000px;height:340px;display:flex}
.type-panel{flex:1;display:flex;flex-direction:column;align-items:center;padding-top:40px;text-align:center}
.type-panel.air{background:var(--blue);color:var(--white)}
.type-panel.cruise{background:var(--yellow);color:var(--ink)}
.type-panel h3{font-size:22px;font-weight:700;margin-top:20px}
.type-panel p{width:330px;font-size:13px;line-height:18px;margin-top:12px}
.type-panel .btn{margin-top:22px}

/* HOT DESTINATION */
.hot{position:absolute;top:1720px;left:0;width:1200px;height:600px}
.hot-head{position:absolute;top:48px;left:100px;width:1000px;height:40px}
.hot-head .section-title{line-height:40px}
.hot-rule{position:absolute;left:0;top:18px;width:70px;height:3px;background:var(--red)}
.hot-arrows{position:absolute;right:0;top:6px;display:flex;gap:6px}
.hot-arrows span{width:28px;height:28px;background:var(--red);display:flex;align-items:center;justify-content:center}
.dest-cards{position:absolute;top:128px;left:100px;width:1000px;display:flex;justify-content:space-between}
.dest-card{width:235px;border:1px solid var(--line)}
.dest-card .photo{height:240px}
.dest-card h4{font-size:13px;font-weight:700;color:var(--ink);line-height:18px;padding:16px 14px 0}
.dest-meta{display:flex;justify-content:space-between;font-size:10px;color:var(--muted);padding:12px 14px;border-bottom:1px solid var(--line);margin:0 0 0}
.dest-foot{display:flex;justify-content:space-between;align-items:center;padding:12px 14px}
.price{font-size:18px;font-weight:700;color:var(--ink)}
.dest-foot .btn{height:26px;line-height:24px;font-size:11px;padding:0 12px}

/* VIDEO */
.video{position:absolute;top:2328px;left:0;width:1200px;height:364px;background:linear-gradient(100deg,#26485a 0%,#3f7c8e 35%,#6ca8a8 55%,#38593a 100%)}
.video-copy{position:absolute;top:56px;left:100px;width:420px;color:var(--white)}
.video-copy .kicker{font-size:15px;letter-spacing:1px;font-weight:400}
.video-copy h2{font-size:60px;font-weight:700;line-height:66px;margin-top:4px}
.video-copy p{font-size:12px;line-height:17px;margin-top:14px;color:#e8f2f4}
.video-copy .btn{margin-top:26px}
.player{position:absolute;top:56px;left:590px;width:510px;height:262px;background:linear-gradient(180deg,#0b1530 0%,#23305c 55%,#b47a2d 100%)}
.player-bar{position:absolute;left:0;bottom:0;width:100%;height:26px;background:rgba(0,0,0,.7);display:flex;align-items:center;padding:0 10px;gap:10px}
.player-track{flex:1;height:3px;background:#666}
.player-track i{display:block;width:28%;height:3px;background:var(--blue)}

/* HAPPY / CLIENTS */
.happy{position:absolute;top:2736px;left:0;width:1200px;height:300px}
.happy-head,.client-head{position:absolute;top:0;display:flex;align-items:center;gap:10px;font-size:20px;font-weight:400;color:var(--ink)}
.happy-head{left:100px}
.client-head{left:780px}
.head-rule{position:absolute;top:38px;height:1px;background:var(--line)}
.happy-photo{position:absolute;top:60px;left:100px;width:320px;height:200px}
.happy-text{position:absolute;top:60px;left:440px;width:300px;font-size:12px;line-height:17px}
.happy-list{list-style:none;margin-top:14px}
.happy-list li{display:flex;align-items:center;gap:8px;color:var(--blue);font-size:11px;line-height:26px}
.quote{position:absolute;top:60px;left:780px;width:320px;border:1px solid var(--line);padding:18px;font-size:12px;line-height:17px;font-style:normal}
.quote-dots{position:absolute;top:170px;left:780px;display:flex;gap:5px}
.quote-dots i{width:7px;height:7px;border-radius:50%;background:#ccc}
.quote-dots i:first-child{background:var(--blue)}
.quote-by{position:absolute;top:168px;left:780px;width:320px;text-align:right;font-size:12px;color:var(--ink);font-weight:500}
.quote-by small{display:block;font-size:10px;color:var(--muted);font-weight:400}

/* FOOTER */
.footer{position:absolute;top:3048px;left:0;width:1200px;height:432px;background:var(--dark);color:#b7b7b7}
.footer-cols{position:absolute;top:44px;left:100px;width:1000px;display:flex;justify-content:space-between}
.footer-col{width:220px}
.footer-col h5{font-size:20px;font-weight:700;color:var(--white);margin-bottom:22px}
.footer-col p,.footer-col li{font-size:12px;line-height:22px}
.footer-col ul{list-style:none}
.footer-col li{border-bottom:1px solid #3a3a3a;line-height:32px}
.tweet{font-size:12px;line-height:17px;margin-bottom:14px}
.tweet b{color:var(--blue);font-weight:400}
.tweet small{display:block;color:#777;font-size:10px}
.input{height:34px;border:1px solid #444;background:#333;color:#888;font-size:11px;line-height:32px;padding:0 10px;margin-bottom:10px}
.input.area{height:76px}
.copyright{position:absolute;top:3480px;left:0;width:1200px;height:48px;background:var(--darker);color:#888;font-size:11px}
.copyright .wrap{line-height:48px}
</style>
</head>
<body>

<section class="hero">
  <div class="hero-photo photo" role="img" aria-label="Photograph of a traveller leaping on a tropical beach under a bright blue sky"></div>
  <div class="topbar">
    <div class="wrap">
      <ul><li>Sign In</li><li>Your Accounts</li><li>Contact Us</li><li>Sitemap</li></ul>
      <ul><li>English ▾</li><li>USD ▾</li><li>Cart (empty) ▾</li></ul>
    </div>
  </div>
  <header class="header">
    <div class="brand"><span class="brand-dot"></span><span class="brand-name">Caldera Key</span></div>
    <ul class="nav">
      <li class="active">HOME</li><li>TOURS</li><li>BLOG</li><li>PAGES</li><li>SHOP</li><li>CONTACT US</li>
    </ul>
    <div class="nav-search"><span>Search</span>
      <svg width="14" height="14" viewBox="0 0 14 14"><circle cx="6" cy="6" r="4.5" fill="none" stroke="#fff" stroke-width="1.6"/><line x1="9.3" y1="9.3" x2="13" y2="13" stroke="#fff" stroke-width="1.6"/></svg>
    </div>
  </header>
  <div class="hero-copy">
    <h1>TRAVEL US WITH BEST DEALS</h1>
    <div class="lead">LOREM IPSUM DOLOR SIT AMET CONSECTETUR ADIPISICING ELITSIA, MOLEST</div>
    <div class="note">Sed ut perspiciatis unde omnis iste natus error sit voluptatem</div>
    <div class="hero-actions">
      <a class="btn btn-yellow">LEARN MORE</a>
      <a class="btn btn-ghost">CHECK OUR PACKAGES</a>
    </div>
  </div>
  <form class="search-tours">
    <div class="search-head"><strong>SEARCH TOURS</strong><span>Find your best tour today!!</span></div>
    <div class="field">Search Tours</div>
    <div class="field">Destination</div>
    <div class="field">Tour Type</div>
    <div class="field wide">Month</div>
    <a class="btn btn-blue">FIND TOURS</a>
  </form>
</section>

<section class="popular">
  <div class="popular-band"></div>
  <h2 class="section-title">MOST POPULAR TOURS</h2>
  <div class="tour-cards">
    <article class="tour-card">
      <div class="photo" role="img" aria-label="Photograph of the Eiffel Tower against a blue sky" style="background:linear-gradient(180deg,#7fb8e6,#b9d6ee 60%,#8d9aa6)"></div>
      <span class="ribbon">FROM $5.49</span>
      <h3>PARIS TOUR</h3>
      <p>Contrary to popular belief, Lorem Ipsum is not simply random text.</p>
      <div class="stars"><svg width="70" height="12" viewBox="0 0 70 12"><g fill="#f5b301"><path id="s" d="M6 0l1.8 3.8 4.2.5-3.1 2.9.8 4.1L6 9.3 2.3 11.3l.8-4.1L0 4.3l4.2-.5z"/><use href="#s" x="14"/><use href="#s" x="28"/><use href="#s" x="42"/><use href="#s" x="56"/></g></svg></div>
      <div class="reviews">23 rating</div>
      <a class="btn">Learn more</a>
    </article>
    <article class="tour-card">
      <div class="photo" role="img" aria-label="Photograph of a London landmark under a blue sky" style="background:linear-gradient(180deg,#3a8fd6,#6fb3e8 60%,#4f7fa8)"></div>
      <span class="round-badge"></span>
      <h3>LONDON TOUR</h3>
      <p>Contrary to popular belief, Lorem Ipsum is not simply random text.</p>
      <div class="stars"><svg width="70" height="12" viewBox="0 0 70 12"><g fill="#f5b301"><use href="#s"/><use href="#s" x="14"/><use href="#s" x="28"/></g><g fill="#ddd"><use href="#s" x="42"/><use href="#s" x="56"/></g></svg></div>
      <div class="reviews">23 rating</div>
      <a class="btn btn-blue">Learn more</a>
    </article>
    <article class="tour-card">
      <div class="photo" role="img" aria-label="Photograph of the Chicago skyline by the river" style="background:linear-gradient(180deg,#8fc3ea,#c9dbe7 55%,#6d7f8c)"></div>
      <span class="ribbon">FROM $5.49</span>
      <h3>CHICAGO TOUR</h3>
      <p>Contrary to popular belief, Lorem Ipsum is not simply random text.</p>
      <div class="stars"><svg width="70" height="12" viewBox="0 0 70 12"><g fill="#f5b301"><use href="#s"/><use href="#s" x="14"/><use href="#s" x="28"/><use href="#s" x="42"/></g><g fill="#ddd"><use href="#s" x="56"/></g></svg></div>
      <div class="reviews">23 rating</div>
      <a class="btn">Learn more</a>
    </article>
  </div>
</section>

<section class="types">
  <div class="photo" role="img" aria-label="Dimmed photograph of a busy city street" style="position:absolute;inset:0;background:linear-gradient(90deg,rgba(0,0,0,.25),rgba(255,255,255,.05),rgba(0,0,0,.25))"></div>
  <h2 class="section-title">FIND TOUR BY TOUR TYPES</h2>
  <div class="type-panels">
    <div class="type-panel air">
      <svg width="44" height="56" viewBox="0 0 44 56"><path d="M22 2C11 2 4 10 4 20c0 10 10 18 14 24h8c4-6 14-14 14-24C40 10 33 2 22 2z" fill="#fff"/><line x1="18" y1="44" x2="18" y2="48" stroke="#fff" stroke-width="2"/><line x1="26" y1="44" x2="26" y2="48" stroke="#fff" stroke-width="2"/><rect x="16" y="48" width="12" height="7" fill="#fff"/></svg>
      <h3>AIR RIDES</h3>
      <p>Contrary to popular belief, Lorem Ipsum is not simply random text. It has roots in a piece of classical Latin literature from 45 BC.</p>
      <a class="btn btn-ghost">Learn More</a>
    </div>
    <div class="type-panel cruise">
      <svg width="60" height="56" viewBox="0 0 60 56"><rect x="24" y="2" width="8" height="10" fill="#222"/><rect x="14" y="12" width="32" height="14" fill="#222"/><path d="M4 28h52l-8 18H12z" fill="#222"/><path d="M2 50c6 0 6 4 12 4s6-4 12-4 6 4 12 4 6-4 12-4 6 4 8 4" fill="none" stroke="#222" stroke-width="2.5"/></svg>
      <h3>CRUISES</h3>
      <p>Contrary to popular belief, Lorem Ipsum is not simply random text. It has roots in a piece of classical Latin literature from 45 BC.</p>
      <a class="btn">Learn More</a>
    </div>
  </div>
</section>

<section class="hot">
  <div class="hot-head">
    <span class="hot-rule"></span>
    <h2 class="section-title">HOT DESTINATION</h2>
    <div class="hot-arrows">
      <span><svg width="10" height="12" viewBox="0 0 10 12"><path d="M8 1L2 6l6 5" fill="none" stroke="#fff" stroke-width="2"/></svg></span>
      <span><svg width="10" height="12" viewBox="0 0 10 12"><path d="M2 1l6 5-6 5" fill="none" stroke="#fff" stroke-width="2"/></svg></span>
    </div>
  </div>
  <div class="dest-cards">
    <article class="dest-card">
      <div class="photo" role="img" aria-label="Photograph of a traveller relaxing on a sandy beach" style="background:linear-gradient(180deg,#6fc0e6,#a8dbe9 50%,#e6d3b0)"></div>
      <h4>CONTRARY TO POPULAR BELIEF FOR EVERYONE</h4>
      <div class="dest-meta"><span>No of Days: 3</span><span>No of People: 4</span></div>
      <div class="dest-foot"><span class="price">$200</span><a class="btn btn-dark">View details</a></div>
    </article>
    <article class="dest-card">
      <div class="photo" role="img" aria-label="Photograph of hot air balloons over a valley" style="background:linear-gradient(180deg,#5fa6d8,#b8d2e2 55%,#a7845c)"></div>
      <h4>CONTRARY TO POPULAR BELIEF FOR EVERYONE</h4>
      <div class="dest-meta"><span>No of Days: 3</span><span>No of People: 4</span></div>
      <div class="dest-foot"><span class="price">$154</span><a class="btn btn-dark">View details</a></div>
    </article>
    <article class="dest-card">
      <div class="photo" role="img" aria-label="Photograph of a smiling traveller in a sun hat by the sea" style="background:linear-gradient(180deg,#3f9bd8,#7fc2e6 55%,#d8b890)"></div>
      <h4>CONTRARY TO POPULAR BELIEF FOR EVERYONE</h4>
      <div class="dest-meta"><span>No of Days: 3</span><span>No of People: 4</span></div>
      <div class="dest-foot"><span class="price">$323</span><a class="btn btn-dark">View details</a></div>
    </article>
    <article class="dest-card">
      <div class="photo" role="img" aria-label="Photograph of red rock canyon at sunset" style="background:linear-gradient(180deg,#c98a4a,#8b3f22 60%,#4a2a1c)"></div>
      <h4>CONTRARY TO POPULAR BELIEF FOR EVERYONE</h4>
      <div class="dest-meta"><span>No of Days: 3</span><span>No of People: 4</span></div>
      <div class="dest-foot"><span class="price">$400</span><a class="btn btn-dark">View details</a></div>
    </article>
  </div>
</section>

<section class="video">
  <div class="photo" role="img" aria-label="Photograph of a tropical lagoon with green cliffs" style="position:absolute;inset:0;background:linear-gradient(180deg,rgba(0,0,0,.1),rgba(0,0,0,.3))"></div>
  <div class="video-copy">
    <div class="kicker">BACKGROUND PARALLAX WITH</div>
    <h2>ANY VIDEO</h2>
    <p>Lorem ipsum dolor sit amet, consectetur adipiscing elit. Morbi sed nisl semper, tincidunt mauris sed, pretium lectus. Nam vitae arcu quis libero feugiat aliquam ut vel nunc. Donec iaculis massa eget nunc efficitur, id dignissim nibh porta.</p>
    <a class="btn btn-ghost">Learn more</a>
  </div>
  <div class="player" role="img" aria-label="Video still of a city lit up at night">
    <div class="player-bar">
      <svg width="10" height="12" viewBox="0 0 10 12"><path d="M0 0l10 6-10 6z" fill="#fff"/></svg>
      <div class="player-track"><i></i></div>
      <svg width="14" height="12" viewBox="0 0 14 12"><path d="M0 4h3l4-4v12L3 8H0z" fill="#fff"/></svg>
    </div>
  </div>
</section>

<section class="happy">
  <h3 class="happy-head"><svg width="18" height="16" viewBox="0 0 18 16"><path d="M9 15S1 10 1 5a4 4 0 0 1 8-1 4 4 0 0 1 8 1c0 5-8 10-8 10z" fill="none" stroke="#1e9be0" stroke-width="1.8"/></svg>We are happy to make you happier</h3>
  <span class="head-rule" style="left:100px;width:640px"></span>
  <h3 class="client-head"><svg width="18" height="16" viewBox="0 0 18 16"><path d="M2 2h14v9H8l-4 4v-4H2z" fill="none" stroke="#1e9be0" stroke-width="1.8"/></svg>What Client Say</h3>
  <span class="head-rule" style="left:780px;width:320px"></span>
  <div class="happy-photo photo" role="img" aria-label="Photograph of a group of smiling friends" style="background:linear-gradient(120deg,#c9a37e,#e6d0b5 50%,#8d7460)"></div>
  <div class="happy-text">
    <p>Contrary to popular belief, Lorem Ipsum is not simply random text. It has roots in a piece of classical Latin literature from 45 BC.</p>
    <ul class="happy-list">
      <li><svg width="10" height="10" viewBox="0 0 10 10"><path d="M1 5l3 3 5-6" fill="none" stroke="#1e9be0" stroke-width="1.6"/></svg>Guided group tours daily</li>
      <li><svg width="10" height="10" viewBox="0 0 10 10"><path d="M1 5l3 3 5-6" fill="none" stroke="#1e9be0" stroke-width="1.6"/></svg>Local guides who know every trail and river</li>
      <li><svg width="10" height="10" viewBox="0 0 10 10"><path d="M1 5l3 3 5-6" fill="none" stroke="#1e9be0" stroke-width="1.6"/></svg>Flexible booking and easy refunds</li>
      <li><svg width="10" height="10" viewBox="0 0 10 10"><path d="M1 5l3 3 5-6" fill="none" stroke="#1e9be0" stroke-width="1.6"/></svg>Secure online payments for every trip</li>
      <li><svg width="10" height="10" viewBox="0 0 10 10"><path d="M1 5l3 3 5-6" fill="none" stroke="#1e9be0" stroke-width="1.6"/></svg>Support from our team all week long</li>
    </ul>
  </div>
  <blockquote class="quote">Contrary to popular belief, Lorem Ipsum is not simply random text. It has roots in a piece of classical Latin literature.</blockquote>
  <div class="quote-dots"><i></i><i></i><i></i></div>
  <div class="quote-by">- Mara Velde<small>CEO OF COMPANY</small></div>
</section>

<footer class="footer">
  <div class="footer-cols">
    <div class="footer-col">
      <h5>Contact</h5>
      <p>Caldera Key</p>
      <p style="margin-top:10px">Avenida Central 12<br>Main Square Office<br>Caldera Key, Panama<br>Phone: +507 555 0142<br>Fax: +507 555 0143<br>hello@calderakey.example</p>
    </div>
    <div class="footer-col">
      <h5>Quick Links</h5>
      <ul><li>Lorem ipsum dolor sit</li><li>Amet consectetur</li><li>Popular tours and trips</li><li>Hot destinations</li><li>Activities and events</li><li>Shop and dine</li></ul>
    </div>
    <div class="footer-col">
      <h5>Latest Tweets</h5>
      <div class="tweet"><b>@calderakey</b> Sunset hikes are back this week, book early. <small>2 days ago</small></div>
      <div class="tweet"><b>@calderakey</b> New river rafting tour now open for groups. <small>3 days ago</small></div>
      <div class="tweet"><b>@calderakey</b> Coffee farm visits every Saturday morning. <small>5 days ago</small></div>
    </div>
    <div class="footer-col">
      <h5>Contact Us</h5>
      <div class="input">Full Name</div>
      <div class="input">Email Address</div>
      <div class="input">Subject</div>
      <div class="input area">Message</div>
      <a class="btn btn-blue">SUBMIT</a>
    </div>
  </div>
</footer>
<div class="copyright"><div class="wrap">Copyright © 2015 CALDERA KEY . All Rights Reserved</div></div>

</body>
</html>
```